Redesign business cards

We have a new logo and I am not that happy with the layout of our existing card and looking for a change. Font is a bit small and the green can be hard to read. Logo may need a tidy up as the copy I have is not that hi-res too so require you to produce a hi-res version of the logo for us too. There will be three individual business cards to produce with just the names and phone numbers being different. Address will change too, but use what you see on the card for now.

Industry/Entity Type

Business

Requirements
Nice to have
• You could consider a redesign to the new logo, just not too radical. We like the blue and green hexagons as we feel that they are representative of oil industry that we are in.

```html
<!DOCTYPE html>
<html lang="en">
<head>
<meta charset="utf-8">
<title>Hexalon Oil Services – Business Cards</title>
<link href="https://fonts.googleapis.com/css2?family=Open+Sans:wght@400;600;700&display=swap" rel="stylesheet">
<style>
  :root {
    --page: #e9e6e1;
    --card-white: #ffffff;
    --brand-blue: #0ea5e6;
    --brand-green: #7cc242;
    --accent-orange: #f7941d;
    --ink-grey: #6d6e71;
    --on-blue: #ffffff;
  }
  * { box-sizing: border-box; margin: 0; padding: 0; }
  html, body {
    width: 1200px; height: 829px; overflow: hidden;
    background: var(--page);
    font-family: "Open Sans", Arial, sans-serif;
  }
  .sheet {
    width: 1200px; height: 829px;
    display: flex; align-items: center; justify-content: center; gap: 60px;
  }
  .card {
    width: 525px; height: 300px; position: relative; overflow: hidden;
    box-shadow: 0 6px 18px rgba(0,0,0,0.18);
  }

  /* Front */
  .card-front { background: var(--card-white); }
  .front-top { height: 162px; position: relative; }
  .wordmark {
    position: absolute; left: 34px; top: 56px;
    display: flex; align-items: center; gap: 12px;
  }
  .wordmark-square { width: 22px; height: 22px; background: var(--brand-blue); }
  .wordmark-name {
    font-weight: 700; font-size: 34px; color: var(--brand-blue); letter-spacing: -0.5px;
  }
  .holder {
    position: absolute; left: 34px; top: 118px;
    font-size: 15px; font-weight: 700; color: var(--accent-orange);
  }
  .holder-role { font-weight: 400; font-size: 12px; color: var(--ink-grey); }
  .divider-line { height: 3px; background: var(--brand-green); }
  .front-band {
    position: absolute; left: 0; right: 0; bottom: 0; height: 135px;
    background: var(--brand-blue); color: var(--on-blue);
    display: flex; padding: 24px 34px; gap: 26px;
  }
  .contact-list { list-style: none; display: flex; flex-direction: column; gap: 10px; font-size: 13px; }
  .contact-item { display: flex; align-items: center; gap: 10px; }
  .contact-icon { width: 14px; height: 14px; flex: none; }
  .address {
    border-left: 1px solid rgba(255,255,255,0.7);
    padding-left: 18px; font-size: 12.5px; line-height: 1.45; font-style: normal;
  }

  /* Back */
  .card-back {
    background: var(--brand-blue); color: var(--on-blue);
    display: flex; flex-direction: column; align-items: center; justify-content: center;
  }
  .back-mark { display: flex; align-items: center; gap: 14px; margin-top: -20px; }
  .back-mark-square { width: 30px; height: 30px; background: var(--on-blue); }
  .back-mark-name { font-size: 40px; font-weight: 700; color: var(--on-blue); }
  .back-web {
    position: absolute; bottom: 46px; left: 0; right: 0; text-align: center;
    font-size: 15px; letter-spacing: 3px;
  }
</style>
</head>
<body>
<main class="sheet">
  <section class="card card-front" aria-label="Business card front">
    <div class="front-top">
      <div class="wordmark">
        <span class="wordmark-square"></span>
        <span class="wordmark-name">Hexalon Oil Services</span>
      </div>
      <p class="holder">Daniel Whitford NZCE (Mech) P&amp;P, <span class="holder-role">Director</span></p>
    </div>
    <div class="divider-line"></div>
    <div class="front-band">
      <ul class="contact-list">
        <li class="contact-item">
          <svg class="contact-icon" viewBox="0 0 16 16"><path d="M3 1.5l3 .5 1 3.5-2 1.2a9 9 0 0 0 4.3 4.3l1.2-2 3.5 1 .5 3c-.3 1-1.4 1.5-2.5 1.4C6.5 13.8 2.2 9.5 1.6 4c-.1-1.1.4-2.2 1.4-2.5z" fill="#fff"/></svg>
          +61 400 555 018
        </li>
        <li class="contact-item">
          <svg class="contact-icon" viewBox="0 0 16 16"><rect x="1" y="3" width="14" height="10" rx="1" fill="none" stroke="#fff" stroke-width="1.5"/><path d="M1.5 3.5L8 9l6.5-5.5" fill="none" stroke="#fff" stroke-width="1.5"/></svg>
          daniel@hexalonoil.co.nz
        </li>
        <li class="contact-item">
          <svg class="contact-icon" viewBox="0 0 16 16"><circle cx="8" cy="8" r="6.5" fill="none" stroke="#fff" stroke-width="1.4"/><ellipse cx="8" cy="8" rx="2.8" ry="6.5" fill="none" stroke="#fff" stroke-width="1.2"/><path d="M1.5 8h13" stroke="#fff" stroke-width="1.2"/></svg>
          www.hexalonoil.com.au
        </li>
      </ul>
      <address class="address">
        Hexalon Oil Services 512 Harbour Road<br>
        PO Box 4417 | Eastbrook<br>
        Queensland 4999
      </address>
    </div>
  </section>

  <section class="card card-back" aria-label="Business card back">
    <div class="back-mark">
      <span class="back-mark-square"></span>
      <span class="back-mark-name">Hexalon</span>
    </div>
    <p class="back-web">www.hexalonoil.com.au</p>
  </section>
</main>
</body>
</html>
```